Business Card Design Project

Business card based on attached logo

Todd Merrick
Todd@lorvantest.com
877-514-9073 ext. 318
Www.LorvanTest.com

Industry/Entity Type

Business

```html
<!DOCTYPE html>
<html lang="en">
<head>
<meta charset="utf-8">
<title>LorvanTest Business Cards</title>
<link rel="stylesheet" href="https://fonts.googleapis.com/css2?family=Open+Sans:wght@400;700&display=swap">
<style>
  :root {
    --stage: #c9a57f;
    --label: #1e1e1e;
    --card-white: #ffffff;
    --card-grey: #ededed;
    --brand-red: #e21d26;
    --deep-red: #b11d22;
    --ink: #111111;
    --text: #3a3a3a;
    --shadow: 0 6px 14px rgba(0,0,0,0.28);
  }
  * { box-sizing: border-box; margin: 0; padding: 0; }
  html, body { width: 1200px; height: 788px; overflow: hidden; }
  body {
    background: var(--stage);
    font-family: "Open Sans", Arial, sans-serif;
    position: relative;
  }
  .view-label {
    position: absolute;
    width: 525px;
    text-align: center;
    font-size: 20px;
    color: var(--label);
  }
  .card {
    position: absolute;
    width: 525px;
    height: 300px;
    border-radius: 22px;
    overflow: hidden;
    box-shadow: var(--shadow);
    background: var(--card-white);
  }
  .card--front  { left: 54px;  top: 74px; }
  .card--back-1 { left: 622px; top: 74px; }
  .card--back-2 { left: 54px;  top: 445px; background: linear-gradient(#d2262c, var(--deep-red)); }
  .card--back-3 { left: 622px; top: 445px; background: linear-gradient(#fafafa, var(--card-grey)); }

  .brand {
    position: absolute;
    left: 0; right: 0;
    display: flex;
    justify-content: center;
    align-items: center;
    gap: 10px;
  }
  .brand__name {
    font-weight: 700;
    font-size: 56px;
    letter-spacing: -1px;
    color: var(--ink);
    line-height: 1;
  }
  .brand__mark {
    width: 16px; height: 16px;
    background: var(--brand-red);
    align-self: flex-start;
    margin-top: 2px;
  }
  .card--back-2 .brand__mark { background: var(--card-white); }

  .contact {
    position: absolute;
    left: 80px;
    top: 200px;
    font-size: 13px;
    color: var(--text);
  }
  .contact__row { display: flex; align-items: center; gap: 5px; height: 22px; }
  .contact__row--split { gap: 5px; }
  .contact__row svg { flex: none; }
  .contact__gap { width: 14px; }

  .name-band { position: absolute; left: 0; top: 250px; width: 525px; height: 50px; }
  .holder-name {
    position: absolute;
    left: 0; right: 0; top: 271px;
    text-align: center;
    color: var(--card-white);
    font-weight: 700;
    font-size: 17px;
  }

  .web {
    position: absolute;
    left: 0; right: 0;
    top: 248px;
    text-align: center;
    font-size: 18px;
    color: var(--text);
  }
  .card--back-2 .web { color: var(--card-white); }

  .plaque {
    position: absolute;
    left: 81px; top: 82px;
    width: 360px; height: 128px;
    background: #f7f7f7;
    border: 1px solid #dadada;
    box-shadow: 0 5px 8px rgba(0,0,0,0.2);
  }
  .plaque .brand__name { font-size: 40px; }
  .plaque .brand__mark { width: 12px; height: 12px; }
</style>
</head>
<body>

  <div class="view-label" style="left:54px; top:33px;">Front</div>
  <div class="view-label" style="left:622px; top:33px;">Back - 1</div>
  <div class="view-label" style="left:54px; top:404px;">Back - 2</div>
  <div class="view-label" style="left:622px; top:404px;">Back - 3</div>

  <section class="card card--front">
    <div class="brand" style="top:62px;">
      <span class="brand__name">LorvanTest</span><span class="brand__mark"></span>
    </div>
    <div class="contact">
      <div class="contact__row">
        <svg width="10" height="10" viewBox="0 0 10 10"><path d="M2 1 L4 1 L4.6 3 L3.4 3.9 Q4.6 6 6.1 6.6 L7 5.4 L9 6 L9 8 Q8 9 6.5 8.6 Q2.5 7 1.2 3 Q1 1.8 2 1 Z" fill="var(--brand-red)"/></svg>
        <span>877-514-9073 ext. 318</span>
      </div>
      <div class="contact__row contact__row--split">
        <svg width="11" height="8" viewBox="0 0 11 8"><rect x="0.5" y="0.5" width="10" height="7" fill="none" stroke="var(--brand-red)"/><path d="M0.5 0.5 L5.5 4.5 L10.5 0.5" fill="none" stroke="var(--brand-red)"/></svg>
        <span>Todd@lorvantest.com</span>
        <span class="contact__gap"></span>
        <svg width="8" height="8" viewBox="0 0 8 8"><circle cx="4" cy="4" r="3.5" fill="var(--brand-red)"/></svg>
        <span>www.LorvanTest.com</span>
      </div>
    </div>
    <svg class="name-band" viewBox="0 0 525 50" preserveAspectRatio="none">
      <path d="M0 22 Q262 2 525 22 L525 50 L0 50 Z" fill="var(--brand-red)"/>
      <path d="M0 17 Q262 -3 525 17" fill="none" stroke="var(--ink)" stroke-width="2"/>
    </svg>
    <div class="holder-name">Todd Merrick</div>
  </section>

  <section class="card card--back-1">
    <div class="brand" style="top:92px;">
      <span class="brand__name">LorvanTest</span><span class="brand__mark"></span>
    </div>
    <div class="web">www.LorvanTest.com</div>
  </section>

  <section class="card card--back-2">
    <div class="brand" style="top:92px;">
      <span class="brand__name">LorvanTest</span><span class="brand__mark"></span>
    </div>
    <div class="web">www.LorvanTest.com</div>
  </section>

  <section class="card card--back-3">
    <div class="plaque">
      <div class="brand" style="top:42px;">
        <span class="brand__name">LorvanTest</span><span class="brand__mark"></span>
      </div>
    </div>
    <div class="web">www.LorvanTest.com</div>
  </section>

</body>
</html>
```